Maple Lantern Productions web site

I need to build a website for a new company I am launching next month. Maple Lantern Productions is a company based in New England that provides sound, lighting, and audio visual services to weddings, corporate, and any other cusomer base looking for quality service for a fair price. Looking for somebody to do a full site not just the image files. I am looking to keep the colors of my logo (orange and black) and possibly grey and white. I am looking to build my site very similar to brightvaleevents.example, which is owned by a friend of mine. I like how he has the big pictures that load in to the site and the basic menu items. I'll need a gallery of photos. The designs should communicate quality, value and trust.
My website address is maplelanternco.example.
Updates

Hi and thanks to everyone for posting such great ideas for our new design.I have some items that I'd like to ask you all to focus on in your revisions.I like how http://www.brightvaleevents.example/ website has five or six high res pictures that change in a slideshow format with a caption that loads in for each one for the different types of services. Try and capture pics like these and with teh same headings as he has. The basic menu designs have been interesting.I am more fond of the menus that are more white with some orange as I dont want it to be too dark. I'm curious to see how your galleries will work and if i'll be able to edit the pages myself? I have some more info on the company for you to fill in:website address is ciderhouseco.comemail: info@ciderhouseco.comaddress: Maple Lantern Productions57 Littlefield StreetAvon, MA 02417"New England's finest DJ's, lighting and sound, video and more. Creating memories one perfect event at a time."Put this under the loading pictures as a tagline.About Cider HouseCider House Productions is a collection of New England's finest talent, ready to make your next event the one you've dreamed of. We have the skills and expertise to deliver your vision of your perfect event. From elegant weddings to themed mitzvah's, corporate av, videography and detail lighting, we offer all of the elements to make your event a success. Added Wednesday, March 1, 2017

Designer's Please also make sure that your design flows well on any device it is being viewed on as well. Thanks. Added Wednesday, March 1, 2017

Project Deadline Extended Reason: Hello designerThank you all very much for your hard work on our project. Im sorry but i need to extend the date of my project. Our parent conpany Rook Nine Prodactions sponsors Bay Youth Assemblies and we are currently at their leadership conference on the Cape. I will be back in on Monday and with your help will get this finished by Thursday the 16th. Thanks Added Thursday, March 9, 2017

Project Deadline Extended Reason: One of the designers is not responding so I now have to make revisions with other designers. I hope to get this website done over the weekends so please get your revisions as soon as possible. Thank you. I am also upgrading the budget another $75 to hopefully get some more interest on my project. Added Wednesday, March 15, 2017

Target Market(s)

Wedding - Corporate -

Industry/Entity Type

It Company

Coding

Coded - Design and coding required

Number of Pages Required

5+ page

Font styles to use
Sans Serif

Requirements
Must have
• Photo Gallery - I want to be able to edit it myself
Nice to have
• I like the look of my friends website brightvaleevents.example

```html
<!DOCTYPE html>
<html lang="en">
<head>
<meta charset="utf-8">
<title>Maple Lantern Productions</title>
<link href="https://fonts.googleapis.com/css2?family=Open+Sans:wght@400;600;700&display=swap" rel="stylesheet">
<style>
:root{
  --orange:#e8572a;
  --ink:#222222;
  --text:#555555;
  --muted:#8a8a8a;
  --line:#dddddd;
  --grey-band:#f1f1f1;
  --white:#ffffff;
  --footer:#2b2b2b;
}
*{box-sizing:border-box;margin:0;padding:0}
html,body{width:1200px;height:4412px;overflow:hidden}
body{font-family:"Open Sans",Arial,sans-serif;color:var(--text);background:var(--white);position:relative}
.abs{position:absolute}

/* header */
.site-header{left:0;top:0;width:1200px;height:124px;background:var(--white)}
.brand{left:132px;top:20px;display:flex;align-items:center;gap:12px}
.brand-mark{width:66px;height:66px;border-radius:50%;background:var(--orange)}
.brand-name{font-weight:700;font-size:22px;line-height:24px;color:var(--ink);text-transform:uppercase;width:200px}
.contact-strip{right:132px;top:22px;display:flex;gap:26px;font-size:14px;font-weight:600;color:var(--ink)}
.contact-strip span{display:flex;align-items:center;gap:7px}
.main-nav{right:132px;top:82px;display:flex;gap:24px;font-size:12.5px;color:var(--text)}
.main-nav .active{color:var(--orange)}

/* hero */
.hero{left:0;top:124px;width:1200px;height:493px;background:linear-gradient(180deg,#e6d8d6 0%,#c8a3a8 40%,#a97f86 60%,#e2d2cf 100%);text-align:center}
.hero-text{left:150px;top:150px;width:900px}
.hero-title{font-size:30px;line-height:40px;font-weight:700;color:var(--white);text-transform:uppercase;letter-spacing:.5px;text-shadow:0 1px 3px rgba(0,0,0,.35)}
.hero-sub{font-size:20px;color:var(--white);margin-top:8px;text-shadow:0 1px 3px rgba(0,0,0,.35)}
.hero-btn{display:inline-block;margin-top:18px;padding:10px 22px;background:rgba(40,40,40,.75);color:var(--white);font-size:19px;font-weight:600}
.hero-arrow{top:352px;width:26px;height:36px;background:rgba(40,40,40,.7);display:flex;align-items:center;justify-content:center}

/* welcome */
.section-title{font-size:22px;font-weight:700;color:var(--orange);text-transform:uppercase;text-align:center;letter-spacing:.5px}
.welcome{left:132px;top:690px;width:936px;text-align:center}
.welcome p{font-size:12px;line-height:19px;margin-top:14px}
.services{left:132px;top:842px;width:936px;display:flex;justify-content:space-between;text-align:center}
.service{width:240px}
.service-icon{width:82px;height:82px;border-radius:50%;background:var(--orange);margin:0 auto;display:flex;align-items:center;justify-content:center}
.service h3{font-size:22px;font-weight:700;color:var(--ink);margin-top:18px;text-transform:uppercase}
.service p{font-size:11.5px;line-height:17px;margin-top:4px}
.divider{left:0;top:1079px;width:1200px;height:1px;background:var(--line)}

/* event rows */
.event-photo{width:447px;height:256px}
.event-body{width:450px}
.event-body h2{font-size:31px;font-weight:400;color:var(--ink)}
.event-body p{font-size:12.5px;line-height:19.5px;margin-top:14px}
.btn-outline{display:inline-block;margin-top:16px;border:1px solid #cfcfcf;padding:7px 13px;font-size:12px;color:var(--text)}

/* team */
.team-band{left:0;top:2508px;width:1200px;height:441px;background:var(--grey-band)}
.team-intro{left:132px;top:2578px;width:936px;text-align:center}
.team-intro p{font-size:12.5px;line-height:19px;margin-top:14px}
.team-grid{left:132px;top:2684px;width:936px;display:flex;justify-content:space-between}
.member{width:168px;height:183px;background:var(--white);border:1px solid var(--line);padding:8px}
.member-photo{width:150px;height:130px;background:linear-gradient(160deg,#e2d3c6,#b49888)}
.member-name{font-size:11px;color:var(--muted);text-align:center;margin-top:14px}

/* testimonials */
.testimonials-title{left:0;top:3022px;width:1200px}
.quote-side{top:3075px;width:140px;height:168px}
.quote-box{left:268px;top:3075px;width:646px;height:168px;border:2px solid #e2e2e2;background:var(--white);padding:26px 40px;text-align:center}
.quote-box p{font-size:12.5px;line-height:19px;color:var(--text)}
.quote-box .who{margin-top:10px;font-size:12.5px}
.quote-avatar{left:571px;top:3215px;width:58px;height:58px;border-radius:50%;background:linear-gradient(160deg,#c9b3a4,#8a766a);border:3px solid var(--white)}
.side-arrow{top:3150px}

/* gallery */
.gallery-title{left:0;top:3345px;width:1200px}
.gallery{left:132px;top:3402px;width:936px;display:grid;grid-template-columns:repeat(4,218px);grid-template-rows:217px 217px;gap:21px;justify-content:space-between}

/* contact */
.contact-band{left:0;top:3940px;width:1200px;height:370px;background:var(--grey-band)}
.contact-title{left:0;top:3983px;width:1200px}
.field{height:41px;background:var(--white);border:1px solid #d6d6d6;font-size:11.5px;color:var(--muted);padding:0 14px;display:flex;align-items:center;justify-content:space-between}
.submit{left:561px;top:4222px;width:78px;height:38px;background:var(--ink);color:var(--white);font-size:12px;font-weight:700;display:flex;align-items:center;justify-content:center}

/* footer */
.site-footer{left:0;top:4310px;width:1200px;height:102px;background:var(--footer)}
.footer-nav{left:132px;top:30px;font-size:11.5px;color:#d6d6d6;display:flex;gap:8px}
.footer-nav i{font-style:normal;color:#777}
.copyright{left:132px;top:60px;font-size:11px;color:#9a9a9a}
.social{right:132px;top:30px;display:flex;gap:10px}
.social span{width:32px;height:32px;border-radius:50%;border:1px solid #888}
</style>
</head>
<body>

<header class="site-header abs">
  <div class="brand abs">
    <span class="brand-mark"></span>
    <span class="brand-name">Maple Lantern Productions</span>
  </div>
  <div class="contact-strip abs">
    <span><svg width="12" height="14" viewBox="0 0 12 14"><rect x="2" y="0.5" width="8" height="13" rx="1.5" fill="none" stroke="#222" stroke-width="1.5"/><circle cx="6" cy="11" r="1" fill="#222"/></svg>555 014 2290</span>
    <span><svg width="14" height="11" viewBox="0 0 14 11"><rect x="0.75" y="0.75" width="12.5" height="9.5" fill="none" stroke="#222" stroke-width="1.5"/><path d="M1 1l6 5 6-5" fill="none" stroke="#222" stroke-width="1.5"/></svg>info@maplelanternco.example</span>
  </div>
  <nav class="main-nav abs">
    <span class="active">Home</span><span>About Us</span><span>Services</span><span>Gallery</span><span>Testimonials</span><span>Events</span><span>Check Availability</span><span>Contact Us</span>
  </nav>
</header>

<section class="hero abs" role="img" aria-label="Slideshow photo: bride and groom embracing in a softly lit wedding reception hall with glowing light trees">
  <div class="hero-text abs">
    <h1 class="hero-title">&ldquo;The Northeast's brightest DJ's, lighting and sound, video and more.</h1>
    <p class="hero-sub">Shaping moments one flawless night at a time.&rdquo;</p>
    <span class="hero-btn">Check Availability</span>
  </div>
</section>
<div class="hero-arrow abs" style="left:0"><svg width="10" height="14"><path d="M8 1L2 7l6 6" fill="none" stroke="#fff" stroke-width="2"/></svg></div>
<div class="hero-arrow abs" style="right:0"><svg width="10" height="14"><path d="M2 1l6 6-6 6" fill="none" stroke="#fff" stroke-width="2"/></svg></div>

<section class="welcome abs">
  <h2 class="section-title">Welcome to Maple Lantern Productions</h2>
  <p>Maple Lantern Productions brings together skilled DJs, lighting designers and sound engineers who care about every detail of your night. From the first call to the final song, our team plans, builds and runs the production so you can relax and enjoy the event. We bring clean sound, warm light and sharp video to weddings, parties, proms and corporate gatherings across the region, always at a fair and honest price.</p>
</section>

<div class="services abs">
  <div class="service">
    <div class="service-icon"><svg width="34" height="30" viewBox="0 0 34 30"><path d="M3 10h7l9-7v24l-9-7H3z" fill="#fff"/><path d="M24 9q4 6 0 12M28 5q7 10 0 20" fill="none" stroke="#fff" stroke-width="2.5" stroke-linecap="round"/></svg></div>
    <h3>Sound</h3>
    <p>Clear, powerful systems tuned for every room and every crowd size.</p>
  </div>
  <div class="service">
    <div class="service-icon"><svg width="26" height="34" viewBox="0 0 26 34"><path d="M13 2a10 10 0 0 0-6 18v4h12v-4A10 10 0 0 0 13 2z" fill="#fff"/><rect x="8" y="26" width="10" height="3" fill="#fff"/><rect x="9.5" y="30" width="7" height="2.5" rx="1" fill="#fff"/></svg></div>
    <h3>Lighting</h3>
    <p>Uplighting, dance floors and pin spots that set the perfect mood.</p>
  </div>
  <div class="service">
    <div class="service-icon"><svg width="30" height="30" viewBox="0 0 30 30"><g stroke="#fff" stroke-width="2.5" stroke-linecap="round"><path d="M6 3v24M15 3v24M24 3v24"/></g><rect x="2" y="16" width="8" height="5" fill="#fff"/><rect x="11" y="7" width="8" height="5" fill="#fff"/><rect x="20" y="13" width="8" height="5" fill="#fff"/></svg></div>
    <h3>Audio Visual</h3>
    <p>Screens, projectors and live video for speeches and presentations.</p>
  </div>
</div>

<div class="divider abs"></div>

<div class="event-photo abs" style="left:132px;top:1161px;background:linear-gradient(135deg,#f0c6e4,#c46fbe 50%,#f4dcea)" role="img" aria-label="Wedding reception hall with draped pink and purple ceiling and a crystal chandelier"></div>
<div class="event-body abs" style="left:617px;top:1165px">
  <h2>Weddings</h2>
  <p>Your wedding day deserves sound and light that feel effortless. We work with your planner and venue to design a ceremony and reception setup that fits your style, from soft candle tones during dinner to a packed dance floor under colour washes and moving lights late into the night.</p>
  <span class="btn-outline">View Packages</span>
</div>

<div class="event-body abs" style="left:132px;top:1500px">
  <h2>Birthday Parties</h2>
  <p>Milestone birthdays, sweet sixteens and surprise parties all get the same care. Our DJs read the room, take requests and keep the energy high, while our lighting crew turns any hall, tent or backyard into a party space your guests will be talking about for years to come.</p>
  <span class="btn-outline">View Packages</span>
</div>
<div class="event-photo abs" style="left:617px;top:1496px;background:linear-gradient(135deg,#3a62b0,#b8402e 50%,#e6a84a)" role="img" aria-label="Child smiling at a birthday cake with lit candles among colourful party guests"></div>

<div class="event-photo abs" style="left:132px;top:1835px;background:linear-gradient(135deg,#9a6a48,#4a3228 50%,#b8855a)" role="img" aria-label="Large auditorium audience facing a lit stage at a school event"></div>
<div class="event-body abs" style="left:617px;top:1839px">
  <h2>School and Formal Events</h2>
  <p>Proms, graduations, assemblies and formals need dependable gear and a crew that knows how schools run. We handle clear microphones for speakers, bright stage lighting for award moments and a safe, well run dance floor, all delivered on time and within the budget your committee has set.</p>
  <span class="btn-outline">View Packages</span>
</div>

<div class="event-body abs" style="left:132px;top:2174px">
  <h2>Corporate Events</h2>
  <p>Conferences, product launches and company dinners run smoothly with our corporate audio visual team. We supply projectors, screens, lecterns and wireless microphones, plus a technician on site for the full program, so every presenter is heard, every slide is sharp and your brand looks its best.</p>
  <span class="btn-outline">View Packages</span>
</div>
<div class="event-photo abs" style="left:617px;top:2170px;background:linear-gradient(135deg,#e4e0dc,#9a9490 55%,#5a5450)" role="img" aria-label="Event host holding a tablet at a corporate conference with seated attendees"></div>

<section class="team-band abs"></section>
<div class="team-intro abs">
  <h2 class="section-title">About Our Team</h2>
  <p>Our crew is a collection of the region's finest talent, ready to make your next event the one you have dreamed of. Meet the people who plan, set up and run every show with skill and care.</p>
</div>
<div class="team-grid abs">
  <div class="member"><div class="member-photo" role="img" aria-label="Team member portrait"></div><div class="member-name">Dana Reyes</div></div>
  <div class="member"><div class="member-photo" role="img" aria-label="Team member portrait"></div><div class="member-name">Dana Reyes</div></div>
  <div class="member"><div class="member-photo" role="img" aria-label="Team member portrait"></div><div class="member-name">Dana Reyes</div></div>
  <div class="member"><div class="member-photo" role="img" aria-label="Team member portrait"></div><div class="member-name">Dana Reyes</div></div>
  <div class="member"><div class="member-photo" role="img" aria-label="Team member portrait"></div><div class="member-name">Dana Reyes</div></div>
</div>

<h2 class="section-title testimonials-title abs">Testimonials</h2>
<div class="quote-side abs" style="left:0;background:linear-gradient(90deg,#fafafa,#e4e4e4)"></div>
<div class="quote-side abs" style="right:0;background:linear-gradient(90deg,#e4e4e4,#fafafa)"></div>
<svg class="side-arrow abs" style="left:130px" width="12" height="20"><path d="M10 2L2 10l8 8" fill="none" stroke="#999" stroke-width="2"/></svg>
<svg class="side-arrow abs" style="right:130px" width="12" height="20"><path d="M2 2l8 8-8 8" fill="none" stroke="#999" stroke-width="2"/></svg>
<div class="quote-box abs">
  <p><b style="font-size:22px;color:#999;line-height:0">&ldquo;</b> From the first meeting to the last dance, the team was calm, friendly and prepared. The lighting transformed our hall and the music kept everyone on the floor all night long. <b style="font-size:22px;color:#999;line-height:0">&rdquo;</b></p>
  <p class="who">&mdash; Dana Reyes</p>
</div>
<div class="quote-avatar abs" role="img" aria-label="Client portrait"></div>

<h2 class="section-title gallery-title abs">Gallery</h2>
<svg class="abs" style="left:132px;top:3352px" width="18" height="14"><path d="M8 1L2 7l6 6M2 7h15" fill="none" stroke="#888" stroke-width="1.6"/></svg>
<svg class="abs" style="left:1050px;top:3352px" width="18" height="14"><path d="M10 1l6 6-6 6M16 7H1" fill="none" stroke="#888" stroke-width="1.6"/></svg>
<div class="gallery abs">
  <div role="img" aria-label="Sound engineer at a mixing desk" style="background:linear-gradient(135deg,#4a7cc0,#22304c)"></div>
  <div role="img" aria-label="Ceiling mounted projector" style="background:linear-gradient(135deg,#eeeeee,#9a9a9a)"></div>
  <div role="img" aria-label="Concert stage with blue light beams" style="background:linear-gradient(135deg,#1a4272,#0c1426 60%,#4a9cd8)"></div>
  <div role="img" aria-label="Children singing in a choir" style="background:linear-gradient(135deg,#ece2d8,#b88464)"></div>
  <div role="img" aria-label="Crowd at a concert under orange stage lights" style="background:linear-gradient(135deg,#f0a030,#a83a1c 55%,#2e1210)"></div>
  <div role="img" aria-label="Colourful stage lights and haze" style="background:linear-gradient(135deg,#3050d0,#d0387e 55%,#201434)"></div>
  <div role="img" aria-label="Close view of a loudspeaker cone" style="background:linear-gradient(135deg,#dcdcdc,#2e2e2e)"></div>
  <div role="img" aria-label="Guitarist performing under purple lights" style="background:linear-gradient(135deg,#40206e,#b0305c 60%,#1e0e2e)"></div>
</div>

<section class="contact-band abs"></section>
<h2 class="section-title contact-title abs">Contact Us</h2>
<div class="field abs" style="left:132px;top:4034px;width:218px">Name</div>
<div class="field abs" style="left:371px;top:4034px;width:218px">Email</div>
<div class="field abs" style="left:610px;top:4034px;width:218px">Phone</div>
<div class="field abs" style="left:850px;top:4034px;width:218px">Service For <svg width="8" height="5"><path d="M0 0h8L4 5z" fill="#666"/></svg></div>
<div class="field abs" style="left:132px;top:4095px;width:218px">Event Type <svg width="8" height="5"><path d="M0 0h8L4 5z" fill="#666"/></svg></div>
<div class="field abs" style="left:371px;top:4095px;width:218px">Month <svg width="8" height="5"><path d="M0 0h8L4 5z" fill="#666"/></svg></div>
<div class="field abs" style="left:610px;top:4095px;width:218px">Date <svg width="8" height="5"><path d="M0 0h8L4 5z" fill="#666"/></svg></div>
<div class="field abs" style="left:850px;top:4095px;width:218px">Year <svg width="8" height="5"><path d="M0 0h8L4 5z" fill="#666"/></svg></div>
<div class="field abs" style="left:132px;top:4157px;width:936px">Message</div>
<div class="submit abs">SUBMIT</div>

<footer class="site-footer abs">
  <nav class="footer-nav abs">
    <span>Home</span><i>|</i><span>About Us</span><i>|</i><span>Services</span><i>|</i><span>Gallery</span><i>|</i><span>Testimonials</span><i>|</i><span>Events</span><i>|</i><span>Check Availability</span><i>|</i><span>Contact Us</span>
  </nav>
  <p class="copyright abs">Copyright &copy; 2017 Company name. All rights reserved.</p>
  <div class="social abs"><span></span><span></span><span></span><span></span></div>
</footer>

</body>
</html>
```